Keystone Trench Co Business Card*

Looking for a professional, clean and crisp business card

I am in the underground utilities industry and am just looking for a really impressive business card. I would like our card to be white with our symbol crisp and clear with it protruding. I also have a business partner that will require his name and info on the card once the design is set. I would like to have our website info on the card which is;
http://keystonetrenchco.example/

Contact Information for Business Card

Website, contact name, number and email

```html
<!DOCTYPE html>
<html lang="en">
<head>
<meta charset="utf-8">
<title>Keystone Trench Co Business Card</title>
<link rel="stylesheet" href="https://fonts.googleapis.com/css2?family=Poppins:wght@400;500&display=swap">
<style>
  :root {
    --page-bg: #ece9e4;
    --card-white: #ffffff;
    --card-dark: #1e1e1e;
    --ink: #1f1d1e;
    --body-grey: #555555;
    --accent-blue: #3b5ba5;
    --accent-red: #e02020;
    --rule-grey: #9a9a9a;
  }
  * { margin: 0; padding: 0; box-sizing: border-box; }
  html, body { width: 1125px; height: 1200px; overflow: hidden; }
  body {
    position: relative;
    background: var(--page-bg);
    font-family: "Poppins", sans-serif;
  }
  .card {
    position: absolute;
    box-shadow: 0 4px 10px rgba(0,0,0,0.25);
  }
  .card-front {
    left: 153px; top: 106px; width: 826px; height: 471px;
    background: var(--card-white);
  }
  .card-back {
    left: 144px; top: 634px; width: 844px; height: 481px;
    background: var(--card-dark);
    display: flex; align-items: center; justify-content: center;
  }
  .brand-front {
    position: absolute;
    left: 130px; top: 155px; width: 200px; height: 160px;
    display: flex; flex-direction: column; align-items: center; justify-content: center; gap: 10px;
    color: var(--ink);
    font-weight: 500; font-size: 26px; line-height: 1.15; text-align: center;
  }
  .brand-mark {
    width: 22px; height: 22px; border-radius: 50%;
    background: var(--ink);
  }
  .divider {
    position: absolute;
    left: 357px; top: 145px; width: 1px; height: 179px;
    background: var(--rule-grey);
  }
  .contact {
    position: absolute;
    left: 394px; top: 139px;
    color: var(--body-grey);
    font-size: 18px; line-height: 23px;
  }
  .contact-name {
    color: var(--accent-blue);
    font-weight: 500; font-size: 26px; line-height: 30px;
  }
  .contact-role {
    color: var(--accent-red);
    font-size: 18px; line-height: 24px;
    margin-bottom: 18px;
  }
  .contact-address { margin-bottom: 17px; }
  .web-bar {
    position: absolute;
    left: 36px; top: 407px; width: 754px; height: 32px;
    background: var(--ink);
    display: flex; align-items: center; justify-content: center;
    color: #ffffff;
    font-size: 18px; letter-spacing: 3.5px;
  }
  .web-bar::before, .web-bar::after {
    content: "";
    position: absolute; top: -4px; width: 5px; height: 40px;
    background: var(--ink);
  }
  .web-bar::before { left: -8px; }
  .web-bar::after { right: -8px; }
  .brand-back {
    display: flex; flex-direction: column; align-items: center; gap: 16px;
    color: #ffffff;
    font-weight: 500; font-size: 52px; line-height: 1.1; text-align: center;
  }
  .brand-back .brand-mark { width: 34px; height: 34px; background: #ffffff; }
</style>
</head>
<body>
  <section class="card card-front" aria-label="Business card front">
    <div class="brand-front">
      <span class="brand-mark"></span>
      <span>Keystone<br>Trench Co</span>
    </div>
    <div class="divider"></div>
    <div class="contact">
      <p class="contact-name">DANIEL HARLOW</p>
      <p class="contact-role">President</p>
      <p class="contact-address">4120 Birchwood Road<br>Fairview, Ontario 58213</p>
      <p>(Ph) 555-014-2738<br>info@keystonetrenchco.example</p>
    </div>
    <div class="web-bar">www.keystonetrenchco.example</div>
  </section>

  <section class="card card-back" aria-label="Business card back">
    <div class="brand-back">
      <span class="brand-mark"></span>
      <span>Keystone Trench Co</span>
    </div>
  </section>
</body>
</html>
```